Software allocation system needs a business card design

We need a business card designed for our software platform - www.tallivo.com.au

At the moment the logo and website is all black and white, we are happy for suggestions on implementing some colour throughout either the logo or business card.

Industry/Entity Type

Software

Font styles to use
Sans Serif

Colors

Designer to choose colors to be used in the design.

```html
<!DOCTYPE html>
<html lang="en">
<head>
<meta charset="utf-8">
<title>Tallivo – Business Card</title>
<link rel="stylesheet" href="https://fonts.googleapis.com/css2?family=Josefin+Sans:wght@300;400&family=Mulish:wght@400;600&display=swap">
<style>
  :root {
    --brand-orange: #e0680f;
    --card-white: #f2f2f2;
    --ink: #2b2b2b;
    --ink-soft: #4a4a4a;
    --backdrop: #dcdad6;
  }
  * { box-sizing: border-box; margin: 0; padding: 0; }
  html, body { width: 1200px; height: 900px; overflow: hidden; }
  body {
    background: var(--backdrop);
    font-family: "Mulish", sans-serif;
    position: relative;
  }
  .card {
    position: absolute;
    left: 250px;
    width: 700px;
    height: 400px;
    border-radius: 4px;
    box-shadow: 0 6px 18px rgba(0,0,0,0.18);
    overflow: hidden;
  }
  .card--back {
    top: 35px;
    background: var(--brand-orange);
    display: flex;
    align-items: center;
    justify-content: center;
  }
  .card--front {
    top: 465px;
    background: var(--card-white);
  }
  .wordmark {
    font-family: "Josefin Sans", sans-serif;
    font-weight: 300;
    letter-spacing: 0.08em;
    display: flex;
    align-items: center;
    gap: 12px;
  }
  .wordmark__dot {
    width: 0.55em;
    height: 0.55em;
    border-radius: 50%;
    background: currentColor;
  }
  .card--back .wordmark { color: #fff; font-size: 46px; }
  .corner-graphic {
    position: absolute;
    left: 0;
    top: 0;
    width: 300px;
    height: 230px;
  }
  .card--front .wordmark {
    position: absolute;
    left: 370px;
    top: 92px;
    color: var(--ink);
    font-size: 48px;
  }
  .identity {
    position: absolute;
    left: 320px;
    top: 180px;
  }
  .identity__name {
    font-size: 15px;
    font-weight: 600;
    letter-spacing: 0.16em;
    color: var(--ink-soft);
    text-transform: uppercase;
  }
  .identity__role {
    font-size: 13px;
    font-weight: 600;
    letter-spacing: 0.12em;
    color: var(--brand-orange);
    margin-top: 4px;
  }
  .contact {
    position: absolute;
    left: 320px;
    top: 238px;
    list-style: none;
    font-size: 14px;
    letter-spacing: 0.06em;
    color: var(--ink);
    line-height: 24px;
  }
  .contact li { display: flex; align-items: center; gap: 10px; }
  .contact svg { width: 13px; height: 13px; flex: none; fill: none; stroke: var(--brand-orange); stroke-width: 2; }
  .contact .no-icon { width: 13px; flex: none; }
</style>
</head>
<body>
  <section class="card card--back" aria-label="Card back">
    <div class="wordmark"><span class="wordmark__dot"></span>TALLIVO</div>
  </section>

  <section class="card card--front" aria-label="Card front">
    <svg class="corner-graphic" viewBox="0 0 300 230" role="img" aria-label="Brand symbol decoration area in orange">
      <path d="M0 0 H300 Q180 120 0 230 Z" fill="var(--brand-orange)"/>
    </svg>

    <div class="wordmark"><span class="wordmark__dot"></span>TALLIVO</div>

    <div class="identity">
      <p class="identity__name">Daniel Koren</p>
      <p class="identity__role">CEO</p>
    </div>

    <ul class="contact">
      <li>
        <svg viewBox="0 0 16 16"><path d="M8 15s5-5 5-9A5 5 0 0 0 3 6c0 4 5 9 5 9z"/><circle cx="8" cy="6" r="1.6"/></svg>
        Lindenweg 12, 5400 Baden, Switzerland
      </li>
      <li>
        <svg viewBox="0 0 16 16"><path d="M3 2h3l1.5 4-2 1.2a8 8 0 0 0 3.3 3.3L10 8.5l4 1.5v3a1.5 1.5 0 0 1-1.5 1.5A11.5 11.5 0 0 1 1.5 3.5 1.5 1.5 0 0 1 3 2z"/></svg>
        +41 56 210 48 36
      </li>
      <li>
        <svg viewBox="0 0 16 16"><rect x="4" y="1.5" width="8" height="13" rx="1.5"/><path d="M7 12h2"/></svg>
        +41 79 402 65 17
      </li>
      <li>
        <svg viewBox="0 0 16 16"><circle cx="8" cy="8" r="3"/><path d="M11 8v1.5a2 2 0 0 0 4 0V8a7 7 0 1 0-3 5.7"/></svg>
        daniel.koren@tallivo.ch
      </li>
      <li>
        <span class="no-icon"></span>
        www.tallivo.com.au
      </li>
    </ul>
  </section>
</body>
</html>
```